Business Card Design Project

- makeup artist business card

- original and creative

- Elegant design

- Feel free to come out with cool designs but stick to being elegant and attractive

- Design relates to makeup

- includes name, occupation, contact numbers, email, website

- regular size business card

- round corner card

- double sided

- on 1 side it should just have the website name in the center " moonveilstudio.net "

Industry/Entity Type

Business

Requirements
Must have
• Delia Marsh
Makeup Artist
USA: +1 (415)772-0461
Singapore: +65 82307915
deliamarsh@moonveilstudio.net
www.moonveilstudio.net
Should not have
• nothing cartoon looking.
Pictures of makeup being grab from the internet.. Examples: eyes or lips.

```html
<!DOCTYPE html>
<html lang="en">
<head>
<meta charset="utf-8">
<title>Moonveil Studio – Business Card</title>
<link rel="stylesheet" href="https://fonts.googleapis.com/css2?family=Arimo:wght@400;700&family=Tinos:wght@700&display=swap">
<style>
  :root {
    --page-bg: #f2e7ea;
    --plum: #8b2169;
    --plum-deep: #761b58;
    --plum-light: #a8357f;
    --orchid: #c2418d;
    --ghost: rgba(214, 120, 178, 0.38);
    --paper: #ffffff;
    --ink: #2a2a2a;
    --sans: "Arimo", Arial, sans-serif;
    --serif: "Tinos", "Times New Roman", serif;
  }
  * { box-sizing: border-box; margin: 0; padding: 0; }
  html, body { width: 1200px; height: 951px; overflow: hidden; }
  body {
    background: radial-gradient(ellipse at 50% 40%, #fbf4f6 0%, var(--page-bg) 75%);
    font-family: var(--sans);
    position: relative;
  }
  .card {
    position: absolute;
    width: 620px;
    height: 354px;
    border-radius: 26px;
    overflow: hidden;
    box-shadow: 0 10px 24px rgba(90, 30, 60, 0.22);
  }

  /* Back side */
  .card--back {
    left: 90px;
    top: 70px;
    background: radial-gradient(ellipse at 35% 30%, var(--plum-light) 0%, var(--plum) 55%, var(--plum-deep) 100%);
  }
  .back-mark {
    position: absolute;
    left: -6px;
    top: 26px;
    font-family: var(--sans);
    font-weight: 400;
    font-size: 62px;
    line-height: 1.05;
    color: var(--ghost);
  }
  .back-mark span { display: block; }
  .back-mark span:nth-child(2) { padding-left: 70px; }
  .back-site {
    position: absolute;
    left: 174px;
    top: 210px;
    font-size: 30px;
    letter-spacing: 1.5px;
    color: var(--paper);
  }

  /* Front side */
  .card--front {
    left: 490px;
    top: 500px;
    background: var(--paper);
  }
  .front-band { position: absolute; inset: 0; }
  .front-mark {
    position: absolute;
    left: 40px;
    top: 26px;
    font-family: var(--sans);
    font-weight: 400;
    font-size: 52px;
    line-height: 1.08;
    color: var(--plum);
  }
  .front-mark span { display: block; }
  .front-mark span:nth-child(2) { padding-left: 52px; }
  .contact-list {
    position: absolute;
    left: 36px;
    top: 206px;
    list-style: none;
    font-size: 17px;
    line-height: 25px;
    color: var(--ink);
  }
  .contact-list li { display: flex; align-items: center; gap: 8px; }
  .contact-icon { width: 14px; height: 14px; flex: none; }
  .contact-list .accent { color: var(--orchid); }
  .person {
    position: absolute;
    right: 34px;
    bottom: 40px;
    text-align: right;
    color: var(--paper);
  }
  .person-name { font-family: var(--serif); font-weight: 700; font-size: 24px; }
  .person-role { font-size: 17px; margin-top: 4px; letter-spacing: 0.5px; }
</style>
</head>
<body>

  <section class="card card--back" aria-label="Card back">
    <div class="back-mark" aria-hidden="true"><span>moonveil</span><span>studio</span></div>
    <p class="back-site">moonveilstudio.net</p>
  </section>

  <section class="card card--front" aria-label="Card front">
    <svg class="front-band" viewBox="0 0 620 354" preserveAspectRatio="none" aria-hidden="true">
      <path d="M380 354 C470 250 500 140 470 0 L620 0 L620 354 Z" fill="var(--orchid)"/>
      <path d="M410 354 C500 250 530 140 510 0 L620 0 L620 354 Z" fill="var(--plum)"/>
    </svg>

    <div class="front-mark"><span>moonveil</span><span>studio</span></div>

    <ul class="contact-list">
      <li>
        <svg class="contact-icon" viewBox="0 0 14 14" aria-hidden="true"><circle cx="7" cy="7" r="6" fill="none" stroke="var(--plum)" stroke-width="1.4"/><path d="M5 4 Q3.8 7 5 10" stroke="var(--plum)" stroke-width="1.6" fill="none" stroke-linecap="round"/></svg>
        USA: +1 (415)772-0461
      </li>
      <li>
        <svg class="contact-icon" viewBox="0 0 14 14" aria-hidden="true"><circle cx="7" cy="7" r="6" fill="none" stroke="var(--plum)" stroke-width="1.4"/><path d="M5 4 Q3.8 7 5 10" stroke="var(--plum)" stroke-width="1.6" fill="none" stroke-linecap="round"/></svg>
        Singapore: +65 82307915
      </li>
      <li>
        <svg class="contact-icon" viewBox="0 0 14 14" aria-hidden="true"><rect x="1" y="3" width="12" height="8" rx="1.5" fill="var(--plum)"/><path d="M1.5 3.5 L7 8 L12.5 3.5" stroke="#fff" stroke-width="1" fill="none"/></svg>
        deliamarsh@moonveilstudio.net
      </li>
      <li>
        <svg class="contact-icon" viewBox="0 0 14 14" aria-hidden="true"><circle cx="7" cy="7" r="6.5" fill="var(--plum)"/></svg>
        <span>www.<span class="accent">moonveilstudio</span>.net</span>
      </li>
    </ul>

    <div class="person">
      <p class="person-name">Delia Marsh</p>
      <p class="person-role">Makeup Artist</p>
    </div>
  </section>

</body>
</html>
```